Business Card Design

It's an investment advisory service for individuals with all there investment needs. Also financial consulting to businesses and governmental agencies on retirement plans etc. It's personalized not commoditized help. Should show strength, knowledge and money orientation.

Reason: Will be out of town setting up office.

Reason: waiting for the 2/3rds of group to vote

Reason: only half the votes are in, I'm calling and getting verbals, but at this time we are down to 2 designs.

Industry/Entity Type

Investment

Contact Information for Business Card

B. Rel K. Financial Consulting and Wealth Management, Berislav Mike Holcek, 5172 Pasadena Loma Verde, San Diego, CA 94417-6381, Registered Investment Advisor

Requirements
Nice to have
• Something money oriented

```html
<!DOCTYPE html>
<html lang="en">
<head>
<meta charset="utf-8">
<title>B. Rel K. Financial Consulting — Business Card</title>
<link rel="stylesheet" href="https://fonts.googleapis.com/css2?family=Lato:wght@400;700;900&family=Mulish:wght@800&display=swap">
<style>
  :root {
    --backdrop: #e9ecef;
    --card-light: #fbfbfb;
    --card-silver: #c9c9c9;
    --ink: #1f1f1f;
    --name-red: #e3141c;
    --band-orange: #f07121;
    --band-blue-light: #16a3e6;
    --band-blue-deep: #1f4fc4;
    --contact-yellow: #f6ef1a;
  }
  * { margin: 0; padding: 0; box-sizing: border-box; }
  html, body {
    width: 1200px;
    height: 900px;
    overflow: hidden;
    background: var(--backdrop);
  }
  .canvas {
    position: relative;
    width: 1200px;
    height: 900px;
  }
  .business-card {
    position: absolute;
    left: 100px;
    top: 164px;
    width: 1000px;
    height: 572px;
    overflow: hidden;
    background: radial-gradient(ellipse at 55% 35%, var(--card-light) 0%, #ececec 45%, var(--card-silver) 100%);
    box-shadow: 0 18px 40px rgba(0, 0, 0, 0.18);
  }
  .card-waves {
    position: absolute;
    inset: 0;
    width: 1000px;
    height: 572px;
  }
  .holder-name {
    position: absolute;
    right: 28px;
    top: 22px;
    font-family: "Lato", sans-serif;
    font-weight: 900;
    font-size: 31px;
    color: var(--name-red);
  }
  .firm-name {
    position: absolute;
    left: 0;
    width: 960px;
    top: 108px;
    text-align: center;
    font-family: "Mulish", sans-serif;
    font-weight: 800;
    font-size: 42px;
    line-height: 52px;
    color: var(--ink);
    letter-spacing: 0.5px;
  }
  .firm-tagline {
    position: absolute;
    left: 0;
    width: 960px;
    top: 222px;
    text-align: center;
    font-family: "Lato", sans-serif;
    font-weight: 400;
    font-size: 33px;
    color: var(--ink);
  }
  .contact {
    position: absolute;
    display: flex;
    align-items: flex-start;
    gap: 14px;
    font-family: "Lato", sans-serif;
    font-weight: 400;
    font-size: 32px;
    line-height: 40px;
    color: var(--contact-yellow);
  }
  .contact-address { left: 36px; top: 438px; }
  .contact-phone { left: 690px; top: 352px; }
  .contact-icon { flex: none; margin-top: 6px; }
</style>
</head>
<body>
<main class="canvas">
  <article class="business-card">
    <svg class="card-waves" viewBox="0 0 1000 572" aria-hidden="true">
      <defs>
        <linearGradient id="blueBand" x1="0" y1="0" x2="0" y2="1">
          <stop offset="0" stop-color="var(--band-blue-light)"/>
          <stop offset="1" stop-color="var(--band-blue-deep)"/>
        </linearGradient>
      </defs>
      <path d="M0 400 C 220 330, 520 300, 760 250 C 880 226, 950 196, 1000 160 L1000 572 L0 572 Z" fill="var(--band-orange)"/>
      <path d="M0 430 C 200 350, 480 325, 740 300 C 870 288, 950 282, 1000 278 L1000 572 L0 572 Z" fill="url(#blueBand)"/>
    </svg>

    <p class="holder-name">Berislav Mike Holcek</p>
    <h1 class="firm-name">B. Rel K. Financial Consulting<br>&amp; Wealth Management</h1>
    <p class="firm-tagline">Registered Investment Advisor</p>

    <p class="contact contact-phone">
      <svg class="contact-icon" width="18" height="28" viewBox="0 0 18 28" aria-hidden="true">
        <path d="M13 2 C6 2 2 8 2 14 C2 20 6 26 13 26 L15 20 C11 20 9 17 9 14 C9 11 11 8 15 8 Z" fill="var(--contact-yellow)"/>
      </svg>
      <span>94417-6381</span>
    </p>

    <p class="contact contact-address">
      <svg class="contact-icon" width="22" height="30" viewBox="0 0 22 30" aria-hidden="true">
        <path d="M11 1 C5 1 1 5.5 1 11 C1 18 11 29 11 29 C11 29 21 18 21 11 C21 5.5 17 1 11 1 Z M11 7 A4 4 0 1 1 11 15 A4 4 0 1 1 11 7 Z" fill="var(--contact-yellow)" fill-rule="evenodd"/>
      </svg>
      <span>5172 Pasadena Loma Verde,<br>San Diego, CA</span>
    </p>
  </article>
</main>
</body>
</html>
```